KTWG application splash screen

We need a 1024x768 image for use as an application splash screen.
The image will be displayed full screen on an 10 inch industrial PC 1024x768 screen while our application is launching. The image should convey that the application is "Waiting for connection to Wi-Fi access point..." and include a graphic of the industrial PC connected to the access point via an Ethernet cable. A list of troubleshooting steps should be included at the bottom of the image. The troubleshooting steps should not be the main focus of the image and should be shown in a smaller font (but still readable at 1024x768 displayed on a 10 inch screen).
I will include a mock up of the general idea of what we are looking for as well as image files for the industrial PC, a screenshot of our application to show on the PC's screen and the AP.
For general look and feel and a sense of corporate branding please review our website https://marrowgatesoilworks.example/. The splash screen should reflect corporate branding.
Target Market(s)
Users of our application
Industry/Entity Type
Agriculture
Look and feel

```html
<!DOCTYPE html>
<html lang="en">
<head>
<meta charset="utf-8">
<title>KTWG – Waiting for Wi-Fi connection</title>
<link href="https://fonts.googleapis.com/css2?family=Poppins:wght@400;600;700&display=swap" rel="stylesheet">
<style>
  :root{
    --page:#ececec;
    --panel-top:#2b2b2b;
    --panel-bottom:#353535;
    --green:#2fb36b;
    --white:#ffffff;
    --text:#e9e9e9;
    --device:#1b1b1d;
    --device-screen:#dfe6e0;
    --ap:#e6e6e6;
    --cable:#111111;
  }
  *{box-sizing:border-box;margin:0;padding:0}
  html,body{width:1200px;height:1103px;overflow:hidden;background:var(--page)}
  body{font-family:"Poppins",sans-serif;position:relative}
  .splash{
    position:absolute;left:111px;top:185px;width:978px;height:733px;
    background:linear-gradient(180deg,var(--panel-top),var(--panel-bottom));
    overflow:hidden;color:var(--white);
  }
  .status-icon{position:absolute;left:461px;top:37px;width:80px;height:68px}
  .headline{
    position:absolute;left:0;right:0;top:124px;text-align:center;
    font-weight:700;font-size:37px;line-height:44px;letter-spacing:-.2px;
  }
  .cab-computer{
    position:absolute;left:102px;top:247px;width:273px;height:218px;
    border-radius:14px;background:var(--device);
    box-shadow:inset 0 0 0 3px #2c2c2e;
  }
  .cab-computer .screen{
    position:absolute;left:26px;top:20px;width:222px;height:166px;
    background:var(--device-screen);border-radius:2px;
  }
  .access-point{
    position:absolute;left:849px;top:241px;width:22px;height:182px;
    background:linear-gradient(90deg,#cfcfcf,var(--ap) 50%,#cfcfcf);border-radius:4px;
  }
  .cable{position:absolute;left:0;top:0;width:978px;height:733px;pointer-events:none}
  .label{position:absolute;font-weight:700;font-size:15px;letter-spacing:.2px;white-space:nowrap}
  .label-computer{left:102px;width:273px;top:478px;text-align:center}
  .label-cable{left:411px;top:453px}
  .label-ap{left:623px;top:360px;line-height:20px}
  .label-ap .model{display:block;font-weight:400;font-size:13.5px;letter-spacing:0}
  .troubleshooting{position:absolute;left:102px;top:526px}
  .troubleshooting h2{
    display:flex;align-items:center;gap:8px;
    color:var(--green);font-weight:600;font-size:16px;margin-bottom:14px;
  }
  .troubleshooting ul{list-style:none;margin-left:8px}
  .troubleshooting li{
    position:relative;padding-left:17px;font-size:12.6px;line-height:20px;color:var(--text);
  }
  .troubleshooting li::before{
    content:"";position:absolute;left:0;top:6px;width:8px;height:8px;border-radius:50%;background:var(--white);
  }
  .brand{
    position:absolute;left:801px;top:652px;font-weight:700;font-size:26px;letter-spacing:1px;color:var(--white);
  }
</style>
</head>
<body>
<main class="splash">
  <svg class="status-icon" viewBox="0 0 80 68" aria-hidden="true">
    <g fill="none" stroke="var(--green)" stroke-width="9" stroke-linecap="round">
      <path d="M6 26 A48 48 0 0 1 74 26"/>
      <path d="M18 39 A31 31 0 0 1 62 39"/>
      <path d="M30 52 A14 14 0 0 1 50 52"/>
      <path d="M12 4 L66 64" stroke="var(--panel-top)" stroke-width="15"/>
      <path d="M12 4 L66 64"/>
    </g>
  </svg>

  <h1 class="headline">Waiting for connection to<br>Wi-Fi access point...</h1>

  <div class="cab-computer" role="img" aria-label="Industrial tractor cab computer showing the seeding application">
    <div class="screen"></div>
  </div>

  <svg class="cable" viewBox="0 0 978 733" aria-hidden="true">
    <rect x="375" y="428" width="14" height="14" rx="2" fill="#2a2a2a"/>
    <path d="M389 435 H860 V423" fill="none" stroke="var(--cable)" stroke-width="3"/>
  </svg>

  <div class="access-point" role="img" aria-label="Outdoor Wi-Fi access point with two antennas"></div>

  <p class="label label-ap">WI-FI ACCESS POINT<span class="model">RANGEMAST AX200-OUTDOOR</span></p>
  <p class="label label-cable">ETHERNET CABLE</p>
  <p class="label label-computer">TRACTOR CAB COMPUTER</p>

  <section class="troubleshooting">
    <h2>
      <svg width="26" height="28" viewBox="0 0 26 28" aria-hidden="true">
        <g fill="none" stroke="var(--green)" stroke-width="1.8">
          <circle cx="13" cy="11" r="8"/>
          <circle cx="13" cy="11" r="4"/>
          <path d="M13 1v2M13 19v2M3 11h2M21 11h2M6 4l1.5 1.5M18.5 16.5L20 18M20 4l-1.5 1.5M7.5 16.5L6 18"/>
          <path d="M3 25h20M6 22l-3 3M20 22l3 3"/>
        </g>
      </svg>
      Troubleshooting steps:
    </h2>
    <ul>
      <li>This screen should only be visible for a short time on boot.</li>
      <li>If this screen stays visible for more than a minute:</li>
      <li>Verify that the Wi-Fi Access Point (AP) powers up when this system does (indicated by a green light on the side of the AP).</li>
      <li>Check the Ethernet cable between this system and the AP for damage, and replace it if necessary.</li>
      <li>Power-cycle this system and wait for it to reboot fully.</li>
      <li>If the issue persists, contact KTWG support for further assistance.</li>
    </ul>
  </section>

  <p class="brand">KTWG</p>
</main>
</body>
</html>
```